Business Card Design For A Renovation Contractor Company

We need a business card for a new company based in Singapore, our company name is "RB Tolvane". We are a renovation contractor that builds designs into reality. We build more of F&B restaurants, retail stores and commercial offices. We work very closely with designers. The final design should communicate to our client that we are a company that you can trust, that will plan and complete your project without giving you a headache. I like my client to remember my company as "RB". The beauty of SIMPLE is important.

Industry/Entity Type

Contractor

Requirements
Nice to have
• Black or Red base

```html
<!DOCTYPE html>
<html lang="en">
<head>
<meta charset="utf-8">
<title>RB Tolvane – Business Card</title>
<link rel="stylesheet" href="https://fonts.googleapis.com/css2?family=Jost:wght@400;500;700&display=swap">
<style>
  :root {
    --brand-red: #e8232a;
    --ink: #1d1d1d;
    --paper: #ffffff;
    --rule: #8a8a8a;
    --backdrop: #eeeae6;
    --soft-text: #3a3a3a;
  }
  * { box-sizing: border-box; margin: 0; padding: 0; }
  html, body {
    width: 1200px;
    height: 720px;
    overflow: hidden;
    background: var(--backdrop);
    font-family: "Jost", sans-serif;
  }
  .canvas { position: relative; width: 1200px; height: 720px; }
  .card {
    position: absolute;
    top: 205px;
    width: 540px;
    height: 310px;
    overflow: hidden;
    box-shadow: 0 6px 18px rgba(0,0,0,0.15);
  }
  .card--front { left: 45px; background: var(--paper); }
  .card--back  { left: 615px; background: var(--brand-red); }

  /* front */
  .front__top-band {
    position: absolute; top: 0; left: 0; right: 0; height: 34px;
    background: var(--brand-red);
    color: var(--paper);
    display: flex; align-items: center; justify-content: center;
    font-weight: 700; font-size: 19px;
  }
  .front__top-band .title { font-weight: 400; font-size: 13px; margin-left: 5px; }
  .front__rule { position: absolute; left: 0; right: 0; height: 1.5px; background: var(--rule); }
  .front__rule--top { top: 40px; }
  .front__rule--bottom { bottom: 46px; }
  .front__bottom-band {
    position: absolute; bottom: 0; left: 0; right: 0; height: 40px;
    background: var(--brand-red);
    color: var(--paper);
    display: flex; align-items: center; justify-content: center;
    font-size: 15px; font-weight: 500; letter-spacing: 0.3px;
  }
  .front__body {
    position: absolute; top: 44px; left: 0; right: 0; bottom: 48px;
    display: flex; flex-direction: column; align-items: center; justify-content: center;
  }
  .brand { display: flex; align-items: center; gap: 10px; }
  .brand__dot { width: 38px; height: 38px; border-radius: 50%; background: var(--brand-red); }
  .brand__name { font-size: 46px; font-weight: 500; color: var(--ink); line-height: 1; }
  .tagline {
    font-size: 16px; color: var(--soft-text); letter-spacing: 0.6px;
    border-top: 1.5px solid var(--ink);
    padding-top: 1px; margin-top: 6px;
  }
  .contact-row {
    display: flex; gap: 16px; align-items: center;
    font-size: 14px; color: var(--soft-text); margin-top: 12px; letter-spacing: 0.4px;
  }
  .contact-row + .contact-row { margin-top: 6px; }
  .contact { display: flex; align-items: center; gap: 5px; white-space: nowrap; }
  .contact svg { width: 11px; height: 11px; fill: var(--brand-red); }
  .web { letter-spacing: 2.5px; }

  /* back */
  .back__brand {
    position: absolute; top: 96px; left: 0; right: 0;
    display: flex; align-items: center; justify-content: center; gap: 14px;
  }
  .back__circle { width: 54px; height: 54px; border-radius: 50%; border: 6px solid var(--paper); }
  .back__name { font-size: 54px; font-weight: 500; color: var(--paper); line-height: 1; }
  .back__web {
    position: absolute; bottom: 34px; right: 48px;
    color: var(--paper); font-size: 18px; letter-spacing: 3px;
  }
</style>
</head>
<body>
<main class="canvas">
  <section class="card card--front" aria-label="Business card front">
    <header class="front__top-band">Your Name,<span class="title">Title</span></header>
    <div class="front__rule front__rule--top"></div>

    <div class="front__body">
      <div class="brand">
        <span class="brand__dot"></span>
        <span class="brand__name">RB Tolvane</span>
      </div>
      <p class="tagline">building reality with a plan</p>

      <div class="contact-row">
        <span class="contact">
          <svg viewBox="0 0 12 12"><circle cx="6" cy="6" r="5.5"/></svg>
          621-438-0975
        </span>
        <span class="contact">
          <svg viewBox="0 0 12 12"><rect x="3" y="0.5" width="6" height="11" rx="1.2"/></svg>
          917-355-2604
        </span>
        <span class="contact">
          <svg viewBox="0 0 12 12"><path d="M0 2h12v8H0z"/></svg>
          info@rbtolvane.com
        </span>
      </div>
      <div class="contact-row">
        <span class="contact web">www.rbtolvane.com</span>
      </div>
    </div>

    <div class="front__rule front__rule--bottom"></div>
    <footer class="front__bottom-band">Door No. Street Name City Name, State, Zip Code.</footer>
  </section>

  <section class="card card--back" aria-label="Business card back">
    <div class="back__brand">
      <span class="back__circle"></span>
      <span class="back__name">RB Tolvane</span>
    </div>
    <p class="back__web">www.rbtolvane.com</p>
  </section>
</main>
</body>
</html>
```